Business Card Design for Occupational Medicine Start Up Company

We need to design a professional business card. We are a healthcare company providing occupational medicine services to blue collar industries. We are professional, efficient and high quality service providers.

Target Market(s)

Blue Collar Industry: Shipbuilding, Ports, Trucking Companies; The Executives and Safety Officers for these companies

Industry/Entity Type

Healthcare

Contact Information for Business Card

Logo, Name, Title, Email, Phone

Other font styles liked:
• Please match our Brand Guide

Requirements
Must have
• Our Company Colors and Logo

```html
<!DOCTYPE html>
<html lang="en">
<head>
<meta charset="utf-8">
<title>CrewCare Clinics Business Card</title>
<link rel="stylesheet" href="https://fonts.googleapis.com/css2?family=Montserrat:wght@400;500;600;700&display=swap">
<style>
  :root {
    --backdrop: #2b2b2b;
    --paper: #f7f7f6;
    --navy: #2e3184;
    --sky: #2e9fd9;
    --amber: #f0a832;
  }
  * { margin: 0; padding: 0; box-sizing: border-box; }
  html, body { width: 1200px; height: 1200px; overflow: hidden; }
  body {
    background: var(--backdrop);
    font-family: "Montserrat", Arial, sans-serif;
    position: relative;
  }
  .card {
    position: absolute;
    width: 594px;
    height: 348px;
    background: var(--paper);
    border-radius: 20px;
    overflow: hidden;
  }
  .card-front { left: 298px; top: 200px; }
  .card-back { left: 293px; top: 637px; }

  .brand {
    display: flex;
    align-items: center;
    gap: 14px;
  }
  .brand-dot {
    width: 22px; height: 22px; border-radius: 50%;
    background: var(--sky);
    flex: none;
  }
  .brand-name {
    color: var(--navy);
    font-weight: 700;
    letter-spacing: 0.5px;
    white-space: nowrap;
  }

  .card-front .brand {
    position: absolute;
    left: 0; right: 0; top: 150px;
    justify-content: center;
  }
  .card-front .brand-name { font-size: 30px; }
  .front-url {
    position: absolute;
    left: 0; right: 0; top: 300px;
    text-align: center;
    font-size: 15px;
    letter-spacing: 0.6px;
    color: var(--navy);
  }
  .front-url .url-core { color: var(--sky); }
  .front-url .url-tail { color: var(--amber); }

  .edge-stripes { position: absolute; left: 0; top: 0; height: 100%; width: 42px; }
  .stripe { position: absolute; top: 0; height: 100%; }
  .stripe-amber { left: 0; width: 14px; background: var(--amber); }
  .stripe-navy { left: 17px; width: 9px; background: var(--navy); }
  .stripe-sky { left: 29px; width: 9px; background: var(--sky); }

  .card-back .brand { position: absolute; left: 71px; top: 52px; }
  .card-back .brand-dot { width: 40px; height: 40px; }
  .card-back .brand-name { font-size: 30px; }

  .person { position: absolute; left: 70px; top: 183px; }
  .person-name {
    color: var(--sky);
    font-weight: 600;
    font-size: 24px;
    letter-spacing: 0.5px;
  }
  .person-title {
    color: var(--navy);
    font-size: 15px;
    margin-top: 2px;
  }

  .contact-list {
    position: absolute;
    left: 70px; top: 252px;
    list-style: none;
  }
  .contact-list li, .address {
    display: flex;
    align-items: center;
    gap: 10px;
    color: var(--navy);
    font-size: 15px;
    line-height: 21px;
  }
  .icon { width: 14px; height: 14px; flex: none; }
  .address {
    position: absolute;
    left: 368px; top: 273px;
    align-items: flex-start;
  }
  .address .icon { margin-top: 3px; }
</style>
</head>
<body>

<section class="card card-front">
  <div class="brand">
    <span class="brand-dot"></span>
    <span class="brand-name">CREWCARE CLINICS</span>
  </div>
  <p class="front-url">www.<span class="url-core">crewcare</span><span class="url-tail">clinics</span>.com</p>
</section>

<section class="card card-back">
  <div class="edge-stripes">
    <span class="stripe stripe-amber"></span>
    <span class="stripe stripe-navy"></span>
    <span class="stripe stripe-sky"></span>
  </div>

  <div class="brand">
    <span class="brand-dot"></span>
    <span class="brand-name">CREWCARE CLINICS</span>
  </div>

  <div class="person">
    <p class="person-name">DANIEL REYES</p>
    <p class="person-title">Senior Doctor</p>
  </div>

  <ul class="contact-list">
    <li>
      <svg class="icon" viewBox="0 0 16 16"><path fill="#2e9fd9" d="M3 2h3l1.5 3.5-2 1.3a8 8 0 0 0 3.7 3.7l1.3-2L14 10v3a1 1 0 0 1-1 1A11 11 0 0 1 2 3a1 1 0 0 1 1-1z"/></svg>
      555-014-2236
    </li>
    <li>
      <svg class="icon" viewBox="0 0 16 16"><rect x="1" y="3" width="14" height="10" fill="#2e3184"/><path d="M1 3l7 6 7-6" fill="none" stroke="#f7f7f6" stroke-width="1.4"/></svg>
      dreyes@crewcareclinics.com
    </li>
    <li>
      <svg class="icon" viewBox="0 0 16 16"><g fill="none" stroke="#f0a832" stroke-width="1.4"><circle cx="8" cy="8" r="6.3"/><ellipse cx="8" cy="8" rx="2.8" ry="6.3"/><path d="M1.7 8h12.6"/></g></svg>
      www.crewcareclinics.com
    </li>
  </ul>

  <div class="address">
    <svg class="icon" viewBox="0 0 16 16"><path fill="#f0a832" d="M8 1a5 5 0 0 0-5 5c0 3.7 5 9 5 9s5-5.3 5-9a5 5 0 0 0-5-5zm0 7a2 2 0 1 1 0-4 2 2 0 0 1 0 4z"/></svg>
    <span>48 Harbor Avenue, Suite 210<br>Portside, State 20417</span>
  </div>
</section>

</body>
</html>
```